Birchline Septic Solutions

Would like to see some single sided ones but would also like to see some double sided with one sided only being the logo. Owners name is Colin Vandro. Phone number is 555-214-0387
Services are pumping, inspections, installs, and repairs

Contact Information for Business Card

555-241-0387 Colin Vandro Harlow Creek, IN

```html
<!DOCTYPE html>
<html lang="en">
<head>
<meta charset="utf-8">
<title>Birchline Septic Solutions – Business Cards</title>
<link href="https://fonts.googleapis.com/css2?family=Montserrat:wght@400;500;700;800&display=swap" rel="stylesheet">
<style>
  :root {
    --teal: #05b8b2;
    --teal-soft: #2fbfb8;
    --ink: #111111;
    --paper: #ffffff;
    --backdrop: #2a2a2a;
  }
  * { box-sizing: border-box; margin: 0; padding: 0; }
  html, body { width: 1200px; height: 880px; overflow: hidden; }
  body {
    background: var(--backdrop);
    font-family: "Montserrat", Arial, sans-serif;
    position: relative;
  }
  .card {
    position: absolute;
    width: 640px;
    height: 366px;
    overflow: hidden;
    box-shadow: 0 10px 30px rgba(0,0,0,.45);
  }
  /* Front: logo side */
  .card-front {
    left: 60px; top: 50px;
    background: var(--teal);
    color: var(--paper);
    display: flex; flex-direction: column; align-items: center; justify-content: center;
    text-align: center;
  }
  .brand-front {
    font-weight: 800;
    font-size: 40px;
    line-height: 1.1;
    letter-spacing: 1px;
    text-transform: uppercase;
  }
  .services {
    margin-top: 34px;
    font-size: 19px;
    font-weight: 500;
    line-height: 1.45;
  }
  .services .item { white-space: nowrap; }
  .tick { width: 16px; height: 16px; vertical-align: -2px; margin: 0 5px 0 8px; }

  /* Back: contact side */
  .card-back {
    left: 500px; top: 464px;
    background: var(--paper);
    color: var(--ink);
  }
  .corner { position: absolute; left: 0; top: 0; width: 640px; height: 366px; }
  .brand-back {
    position: absolute;
    left: 44px; top: 130px;
    width: 280px;
    font-weight: 800;
    font-size: 30px;
    line-height: 1.15;
    text-transform: uppercase;
    color: var(--ink);
  }
  .divider {
    position: absolute;
    left: 340px; top: 96px;
    width: 2px; height: 150px;
    background: var(--teal);
  }
  .contact {
    position: absolute;
    left: 362px; top: 96px;
    white-space: nowrap;
  }
  .name { font-weight: 800; font-size: 28px; letter-spacing: .5px; }
  .name .last { color: var(--teal); }
  .role { font-size: 15px; margin-top: 2px; }
  .line { display: flex; align-items: center; gap: 8px; font-size: 15px; margin-top: 10px; }
  .line svg { width: 16px; height: 16px; flex: none; }
</style>
</head>
<body>

<section class="card card-front">
  <h1 class="brand-front">Birchline<br>Septic Solutions</h1>
  <div class="services">
    <div class="item"><svg class="tick" viewBox="0 0 16 16"><circle cx="8" cy="8" r="6.5" fill="none" stroke="#fff" stroke-width="2"/><path d="M4.8 8.2l2.2 2.2 4.2-4.6" fill="none" stroke="#fff" stroke-width="2"/></svg>Services are pumping</div>
    <div class="item"><svg class="tick" viewBox="0 0 16 16"><circle cx="8" cy="8" r="6.5" fill="none" stroke="#fff" stroke-width="2"/><path d="M4.8 8.2l2.2 2.2 4.2-4.6" fill="none" stroke="#fff" stroke-width="2"/></svg>inspections<svg class="tick" viewBox="0 0 16 16"><circle cx="8" cy="8" r="6.5" fill="none" stroke="#fff" stroke-width="2"/><path d="M4.8 8.2l2.2 2.2 4.2-4.6" fill="none" stroke="#fff" stroke-width="2"/></svg>installs<svg class="tick" viewBox="0 0 16 16"><circle cx="8" cy="8" r="6.5" fill="none" stroke="#fff" stroke-width="2"/><path d="M4.8 8.2l2.2 2.2 4.2-4.6" fill="none" stroke="#fff" stroke-width="2"/></svg>and repairs</div>
  </div>
</section>

<section class="card card-back">
  <svg class="corner" viewBox="0 0 640 366" aria-hidden="true">
    <polygon points="400,336 640,234 640,366 470,366" fill="var(--teal-soft)"/>
    <polygon points="400,344 470,366 380,366" fill="var(--ink)"/>
  </svg>
  <h2 class="brand-back">Birchline<br>Septic<br>Solutions</h2>
  <div class="divider"></div>
  <div class="contact">
    <div class="name">COLIN <span class="last">VANDRO</span></div>
    <div class="role">Owners</div>
    <div class="line">
      <svg viewBox="0 0 16 16"><path d="M3 2h3l1.5 3.5-2 1.3a8 8 0 0 0 3.7 3.7l1.3-2L14 10v3a1 1 0 0 1-1 1A11 11 0 0 1 2 3a1 1 0 0 1 1-1z" fill="var(--teal)"/></svg>
      <span>555-214-0387</span>
    </div>
    <div class="line">
      <svg viewBox="0 0 16 16"><path d="M8 1a5 5 0 0 0-5 5c0 4 5 9 5 9s5-5 5-9a5 5 0 0 0-5-5z" fill="var(--teal)"/><circle cx="8" cy="6" r="2" fill="#fff"/></svg>
      <span>Colin Vandro Harlow Creek, IN</span>
    </div>
  </div>
</section>

</body>
</html>
```